Modern Business Card

Modern professional business card with more than just logo and demographic info. Something memorable.

We are a trendy/modern chiropractic group with an emphasis on neurology, hence the minimalist-type brain logo. We want to convey that modern and technical aspect with professionalism and the elite nature of our practice environment.

```html
<!DOCTYPE html>
<html lang="en">
<head>
<meta charset="utf-8">
<title>Verity Chiropractic – Business Card</title>
<link href="https://fonts.googleapis.com/css2?family=Open+Sans:wght@400;600;700&display=swap" rel="stylesheet">
<style>
  :root {
    --backdrop: #3b3531;
    --card: #242528;
    --card-edge: #3a6fc6;
    --emboss: #2e2f33;
    --emboss-shadow: #1a1b1d;
    --ink-light: #e9eaec;
    --ink-blue: #3f78d1;
  }
  * { box-sizing: border-box; margin: 0; padding: 0; }
  html, body {
    width: 1200px; height: 847px; overflow: hidden;
    background: var(--backdrop);
    font-family: "Open Sans", Arial, sans-serif;
  }
  .canvas {
    position: relative; width: 1200px; height: 847px;
    display: flex; align-items: center; justify-content: center; gap: 44px;
  }
  .card {
    position: relative; width: 540px; height: 309px;
    background: var(--card);
    border-bottom: 4px solid var(--card-edge);
    box-shadow: 0 14px 30px rgba(0,0,0,.45);
  }
  /* back side */
  .card-back .brand-emboss {
    position: absolute; right: 46px; bottom: 56px;
    font-weight: 600; font-size: 40px; letter-spacing: 1px; line-height: 1.05;
    color: var(--emboss);
    text-align: left; text-transform: uppercase;
    text-shadow: 0 1px 0 var(--emboss-shadow);
  }
  .card-back .brand-square {
    position: absolute; left: 50px; top: 40px;
    width: 150px; height: 150px; background: var(--emboss);
  }
  /* front side */
  .card-front { display: flex; align-items: center; padding: 0 34px; }
  .brand {
    display: flex; align-items: center; gap: 12px; width: 238px;
  }
  .brand-square { width: 34px; height: 34px; background: var(--ink-blue); flex: none; }
  .brand-name {
    font-weight: 600; font-size: 21px; line-height: 1.1;
    color: var(--ink-light); text-transform: uppercase; letter-spacing: .5px;
  }
  .divider {
    width: 2px; height: 148px; background: var(--ink-blue); margin: 0 22px 0 8px;
  }
  .details { color: var(--ink-light); font-size: 14px; line-height: 1.45; }
  .details .name {
    color: var(--ink-blue); font-weight: 700; font-size: 19px;
    text-transform: uppercase; letter-spacing: .5px; line-height: 1.2;
  }
  .details .role { margin-bottom: 8px; }
  .details .address { margin-bottom: 8px; }
  .contact { display: flex; align-items: center; gap: 6px; }
  .contact svg { width: 12px; height: 12px; fill: var(--ink-light); flex: none; }
</style>
</head>
<body>
<main class="canvas">
  <section class="card card-back" aria-label="Card back">
    <div class="brand-square"></div>
    <div class="brand-emboss">Verity<br>Chiropractic</div>
  </section>

  <section class="card card-front" aria-label="Card front">
    <div class="brand">
      <div class="brand-square"></div>
      <div class="brand-name">Verity<br>Chiropractic</div>
    </div>
    <div class="divider"></div>
    <div class="details">
      <div class="name">Dan Harlow</div>
      <div class="role">President</div>
      <div class="address">1820 Marina Crest Way<br>Seabrook CA 90000</div>
      <div class="contact">
        <svg viewBox="0 0 24 24"><path d="M6.6 10.8a15.1 15.1 0 0 0 6.6 6.6l2.2-2.2c.3-.3.7-.4 1-.2 1.1.4 2.3.6 3.6.6.6 0 1 .4 1 1V20c0 .6-.4 1-1 1A17 17 0 0 1 3 4c0-.6.4-1 1-1h3.5c.6 0 1 .4 1 1 0 1.3.2 2.5.6 3.6.1.3 0 .7-.2 1z"/></svg>
        <span>555-014-2237</span>
      </div>
      <div class="contact">
        <svg viewBox="0 0 24 24"><path d="M2 5h20v14H2z M2 5l10 8 10-8" /></svg>
        <span>dan@veritychiro.com</span>
      </div>
      <div class="contact">
        <svg viewBox="0 0 24 24"><circle cx="12" cy="12" r="10"/></svg>
        <span>www.veritychiro.com</span>
      </div>
    </div>
  </section>
</main>
</body>
</html>
```